Presentation Of Our Epidemiology Consulting Framework

We need a slide deck (png files) for PowerPoint that describes our organization and type of clients we serve, and our 6 phase framework that explains how we work with clients. Please use the minimum amount of text on each slide.  We want a more visual display of how to work with us. We want it to look very similar to our brochure.  We want to also have a few extra branded slides without text that can be used as a template if we decide to add to the deck later or create a new slide deck.
Colors
#56588C
#F28444
#F2E088
#F24C27
#ODODOD

```html
<!DOCTYPE html>
<html lang="en">
<head>
<meta charset="utf-8">
<title>Epidemiology Consulting Framework – Slide Deck</title>
<link href="https://fonts.googleapis.com/css2?family=Bebas+Neue&family=Poppins:wght@400;500;600;700&display=swap" rel="stylesheet">
<style>
:root{
  --board:#525252;
  --navy:#1c1b4f;
  --navy-deep:#141340;
  --purple:#56588C;
  --orange:#F28444;
  --red:#F24C27;
  --ink:#0D0D0D;
  --paper:#f4f4f7;
  --white:#ffffff;
}
*{box-sizing:border-box;margin:0;padding:0}
html,body{width:1026px;height:1200px;overflow:hidden;background:var(--board)}
body{position:relative;font-family:'Poppins',sans-serif;color:var(--ink)}
.slide{position:absolute;width:444px;height:249px;overflow:hidden;
  background:linear-gradient(120deg,#ffffff 0%,#eeeef3 30%,#ffffff 45%,#ececf2 65%,#ffffff 80%,#f0f0f5 100%);
  box-shadow:0 4px 10px rgba(0,0,0,.35)}
.col-l{left:51px}.col-r{left:531px}
.row1{top:54px}.row2{top:335px}.row3{top:616px}.row4{top:897px}
.abs{position:absolute}
.display{font-family:'Bebas Neue',sans-serif;font-weight:400;letter-spacing:.2px;line-height:1}
.hl{color:var(--orange)}

/* header */
.slide-title{position:absolute;left:25px;top:12px;font-size:19px;color:var(--navy)}
.title-rule{position:absolute;left:0;top:33px;width:50px;height:1.5px;background:var(--red)}
.title-rule::after{content:"";position:absolute;right:-3px;top:-2.5px;width:6px;height:6px;border-radius:50%;background:var(--red)}
.subtitle{position:absolute;left:0;width:100%;text-align:center;font-size:13.5px;color:var(--navy)}

/* footer */
.footer-bar{position:absolute;left:0;top:228px;width:272px;height:17px;background:var(--navy);display:flex;align-items:center;padding-left:25px;color:var(--white);font-size:6.5px}
.mail-dot{width:9px;height:9px;border-radius:50%;background:var(--red);margin-right:6px;display:flex;align-items:center;justify-content:center}
.page-no{position:absolute;right:4px;top:3px;width:11px;height:11px;border-radius:50%;background:var(--white);color:var(--navy);font-size:5px;font-weight:700;display:flex;align-items:center;justify-content:center}
.brand{display:flex;align-items:center;gap:4px;font-weight:700;color:var(--purple);white-space:nowrap}
.brand::before{content:"";width:.7em;height:.7em;border-radius:50%;background:var(--orange)}
.footer-brand{position:absolute;left:290px;top:228px;font-size:16px}

/* cover */
.cover-top{position:absolute;left:0;top:0;width:100%;height:196px;background:linear-gradient(120deg,#15144a 0%,#23226a 55%,#1a1958 100%)}
.cover-title{position:absolute;top:21px;width:100%;text-align:center;font-size:23px;color:var(--white)}
.pill{position:absolute;left:174px;top:79px;width:96px;height:21px;border-radius:11px;background:var(--red);border:1px solid var(--white);color:var(--white);font-size:8px;font-weight:500;display:flex;align-items:center;justify-content:center}
.cover-kicker{position:absolute;top:117px;width:100%;text-align:center;font-size:15px;color:var(--orange)}
.cover-text{position:absolute;left:50px;top:139px;width:344px;text-align:center;font-size:5.9px;line-height:10.3px;color:#dcdcec}
.center-brand{position:absolute;left:0;width:100%;justify-content:center;font-size:24px}

/* discovery & impact rings */
.ring{position:absolute;border:1px dashed #b7b7c6;border-radius:50%}
.hub{position:absolute;border-radius:50%;background:var(--white);box-shadow:0 4px 10px rgba(0,0,0,.15);display:flex;align-items:center;justify-content:center}
.node{position:absolute;width:25px;height:25px;border-radius:50%;background:var(--navy);display:flex;align-items:center;justify-content:center;box-shadow:0 2px 4px rgba(0,0,0,.2)}
.pin{position:absolute;width:5px;height:5px;border-radius:50%;background:var(--white);border:1.5px solid var(--red)}
.node-label{position:absolute;font-size:6px;font-weight:500;line-height:9px;color:var(--ink)}

/* bullets */
.bullet-list{position:absolute;list-style:none}
.bullet-list li{position:relative;padding-left:17px}
.bullet-list li::before{content:"";position:absolute;left:0;top:.35em;width:7px;height:7px;border-radius:50%;background:var(--red)}
.bullet-list li::after{content:"";position:absolute;left:1.8px;top:calc(.35em + 2.3px);width:2px;height:2px;border-top:1px solid #fff;border-right:1px solid #fff;transform:rotate(45deg)}
.launch-list{left:25px;top:103px;font-size:7.6px;font-weight:500}
.launch-list li{margin-bottom:7.2px;line-height:10px}
.small-list{left:242px;font-size:5.8px;font-weight:500}
.small-list li{padding-left:14px;line-height:8.2px}
.small-list li::before{width:5px;height:5px;top:.25em}
.small-list li::after{left:1.1px;top:calc(.25em + 1.6px);width:1.5px;height:1.5px}

.photo{position:absolute;border-radius:6px}

/* step cards */
.card{position:absolute;width:90px;height:87px;background:var(--white);border-radius:6px;box-shadow:0 3px 8px rgba(0,0,0,.18);padding:30px 12px 0 12px;font-size:7.8px;font-weight:500;line-height:11px;color:var(--ink)}
.card.outlined{border:1px solid var(--orange);border-top:none}
.badge{position:absolute;left:12px;top:-17px;width:34px;height:34px;border-radius:50%;background:var(--red);display:flex;align-items:center;justify-content:center;box-shadow:0 0 0 2px #fde3d6}
.badge.soft{background:var(--orange)}

/* closing */
.close-top{position:absolute;left:0;top:0;width:100%;height:196px;background:linear-gradient(120deg,#1a1958 0%,#23226a 60%,#1c1b55 100%)}
.close-title{position:absolute;left:25px;top:46px;font-size:22.5px;color:var(--white)}
.close-text{position:absolute;left:25px;top:100px;width:265px;font-size:9.3px;line-height:13px;color:var(--white)}
.mail-pill{position:absolute;left:25px;top:133px;width:119px;height:17px;border-radius:9px;background:var(--red);border:1px solid var(--white);color:var(--white);font-size:6.6px;font-weight:500;display:flex;align-items:center;justify-content:center;gap:4px}
</style>
</head>
<body>

<!-- 01 Cover -->
<section class="slide col-l row1">
  <div class="cover-top" role="img" aria-label="Dark navy background with a faded photo of a public health professional"></div>
  <h1 class="cover-title display">Transforming Health Data Into<br>Community Impact</h1>
  <div class="pill">The DrALMorrow</div>
  <h2 class="cover-kicker display">Framework</h2>
  <p class="cover-text">DrALMorrow LLC is an epidemiology consulting firm that supports large nonprofit organizations and government agencies that serve black, indigenous, and people of color commonly referred to as BIPOC communities. Our diverse team of innovative global public health professionals are ready to serve your organization by helping you address your most pressing challenges.</p>
  <div class="brand center-brand" style="top:208px">Dr ALMorrow</div>
</section>

<!-- 02 Discovery -->
<section class="slide col-l row2">
  <h2 class="slide-title display">Discovery &amp; <span class="hl">Vision Alignment</span></h2>
  <div class="title-rule"></div>
  <h3 class="subtitle display" style="top:47px">Building the Foundation for Success</h3>
  <div class="ring" style="left:61px;top:83px;width:124px;height:124px"></div>
  <div class="hub" style="left:73px;top:95px;width:100px;height:100px"><span class="brand" style="font-size:11px">Dr ALMorrow</span></div>
  <div class="pin" style="left:164px;top:100px"></div>
  <div class="pin" style="left:179px;top:123px"></div>
  <div class="pin" style="left:181px;top:150px"></div>
  <div class="pin" style="left:168px;top:182px"></div>
  <div class="node" style="left:174px;top:76px"><svg width="12" height="12" viewBox="0 0 12 12"><circle cx="6" cy="6" r="5" fill="none" stroke="#F28444" stroke-width="1.3"/><circle cx="6" cy="6" r="2" fill="#F28444"/></svg></div>
  <div class="node" style="left:192px;top:109px"><svg width="12" height="12" viewBox="0 0 12 12"><circle cx="6" cy="5" r="3.5" fill="none" stroke="#F28444" stroke-width="1.3"/><rect x="4.5" y="8.5" width="3" height="2.5" fill="#F28444"/></svg></div>
  <div class="node" style="left:192px;top:145px"><svg width="12" height="12" viewBox="0 0 12 12"><path d="M6 1a3.5 3.5 0 0 0-2 6.3V9h4V7.3A3.5 3.5 0 0 0 6 1z" fill="#F28444"/><rect x="4.5" y="10" width="3" height="1.2" fill="#F28444"/></svg></div>
  <div class="node" style="left:176px;top:183px"><svg width="12" height="12" viewBox="0 0 12 12"><path d="M1 11V8h3v3M5 11V6h3v5M9 11V3h2v8" fill="#F28444"/></svg></div>
  <p class="node-label" style="left:208px;top:80px;width:180px">Deep-dive exploration of your organization's unique challenges and opportunities</p>
  <p class="node-label" style="left:224px;top:117px">Strategic alignment of goals and expectations</p>
  <p class="node-label" style="left:224px;top:153px">Custom-tailored solution design</p>
  <p class="node-label" style="left:208px;top:192px">Clear roadmap development with defined</p>
  <div class="footer-bar"><span class="mail-dot"></span>support@dralmorrow.com<span class="page-no">02</span></div>
  <div class="brand footer-brand">Dr ALMorrow</div>
</section>

<!-- 03 Partnership -->
<section class="slide col-l row3">
  <h2 class="slide-title display">Partnership <span class="hl">Launch</span></h2>
  <div class="title-rule"></div>
  <h3 class="abs display" style="left:25px;top:65px;font-size:15.5px;color:var(--navy)">Setting the Stage for<br>Excellence</h3>
  <ul class="bullet-list launch-list">
    <li>Formation of dedicated project team</li>
    <li>Establishment of collaborative workflow</li>
    <li>Comprehensive data gathering</li>
    <li>Strategic timeline planning</li>
    <li>Stakeholder engagement and vision<br>capture</li>
  </ul>
  <div class="photo" style="left:222px;top:52px;width:196px;height:156px;background:linear-gradient(135deg,#1d3f6e 0%,#5d8fc4 45%,#c9dcee 100%)" role="img" aria-label="Photo of a scientist pointing at data charts on a computer monitor"></div>
  <div class="footer-bar"><span class="mail-dot"></span>support@dralmorrow.com<span class="page-no">03</span></div>
  <div class="brand footer-brand">Dr ALMorrow</div>
</section>

<!-- 04 Expert Execution -->
<section class="slide col-l row4">
  <h2 class="slide-title display">Expert <span class="hl">Execution</span></h2>
  <div class="title-rule"></div>
  <h3 class="subtitle display" style="top:48px">Where Science Meets Service</h3>
  <p class="abs" style="top:71px;width:100%;text-align:center;font-size:8.4px;font-weight:500">Our specialized team begins the transformation process:</p>
  <div class="card" style="left:25px;top:109px">
    <span class="badge"><svg width="16" height="16" viewBox="0 0 16 16"><path d="M2 14V10h2v4M6 14V7h2v7M10 14V9h2v5" fill="#fff"/><path d="M2 8l4-4 3 2 5-4" fill="none" stroke="#fff" stroke-width="1.3"/></svg></span>
    In-depth research and analysis
  </div>
  <div class="card outlined" style="left:126px;top:126px">
    <span class="badge soft"><svg width="16" height="16" viewBox="0 0 16 16"><circle cx="7" cy="6" r="4" fill="none" stroke="#fff" stroke-width="1.4"/><rect x="8" y="8" width="6" height="7" fill="#fff"/></svg></span>
    Content development and refinement
  </div>
  <div class="card" style="left:227px;top:109px">
    <span class="badge"><svg width="16" height="16" viewBox="0 0 16 16"><rect x="6" y="2" width="9" height="8" fill="none" stroke="#fff" stroke-width="1.3"/><circle cx="3" cy="5" r="1.8" fill="#fff"/><rect x="1.5" y="7.5" width="3" height="7" fill="#fff"/></svg></span>
    Data interpretation and visualization
  </div>
  <div class="card outlined" style="left:328px;top:126px">
    <span class="badge soft"><svg width="16" height="16" viewBox="0 0 16 16"><rect x="2" y="2" width="12" height="12" rx="1" fill="none" stroke="#fff" stroke-width="1.3"/><circle cx="6" cy="7" r="1.8" fill="#fff"/><path d="M3.5 12a2.5 2.5 0 0 1 5 0M10 6h3M10 9h3" stroke="#fff" stroke-width="1.2" fill="none"/></svg></span>
    Plain language translation of complex health information
  </div>
  <div class="footer-bar"><span class="mail-dot"></span>support@dralmorrow.com<span class="page-no">04</span></div>
  <div class="brand footer-brand">Dr ALMorrow</div>
</section>

<!-- 05 Collaborative Refinement -->
<section class="slide col-r row1">
  <h2 class="slide-title display">Collaborative <span class="hl">Refinement</span></h2>
  <div class="title-rule"></div>
  <h3 class="subtitle display" style="top:51px">Ensuring Perfect Alignment</h3>
  <div class="abs" style="left:0;top:127px;width:100%;height:97px;background:linear-gradient(90deg,#4e5090 0%,#6a6ca3 50%,#54568f 100%)" role="img" aria-label="Purple-tinted photo of researchers working in a laboratory"></div>
  <div class="card" style="left:25px;top:94px;height:74px">
    <span class="badge"><svg width="16" height="16" viewBox="0 0 16 16"><rect x="2" y="3" width="12" height="8" fill="none" stroke="#fff" stroke-width="1.3"/><path d="M5 10V7M8 10V5M11 10V8M8 11v3" stroke="#fff" stroke-width="1.3"/></svg></span>
    Presentation of initial frameworks
  </div>
  <div class="card" style="left:126px;top:94px;height:74px">
    <span class="badge soft"><svg width="16" height="16" viewBox="0 0 16 16"><rect x="2" y="5" width="12" height="8" rx="1" fill="#fff"/><path d="M4 3h8" stroke="#fff" stroke-width="1.3"/></svg></span>
    Interactive feedback sessions
  </div>
  <div class="card" style="left:227px;top:94px;height:74px">
    <span class="badge"><svg width="16" height="16" viewBox="0 0 16 16"><circle cx="8" cy="8" r="5.5" fill="none" stroke="#fff" stroke-width="1.6" stroke-dasharray="2 1.5"/><circle cx="8" cy="8" r="2.3" fill="#fff"/></svg></span>
    Draft review and optimization
  </div>
  <div class="card" style="left:328px;top:94px;height:74px">
    <span class="badge soft"><svg width="16" height="16" viewBox="0 0 16 16"><circle cx="8" cy="8" r="5" fill="none" stroke="#fff" stroke-width="2" stroke-dasharray="2 1.6"/><circle cx="8" cy="8" r="1.8" fill="#fff"/></svg></span>
    Stakeholder input integration
  </div>
  <div class="footer-bar"><span class="mail-dot"></span>support@dralmorrow.com<span class="page-no">05</span></div>
  <div class="brand footer-brand">Dr ALMorrow</div>
</section>

<!-- 06 Impact Delivery -->
<section class="slide col-r row2">
  <h2 class="slide-title display">Impact <span class="hl">Delivery</span></h2>
  <div class="title-rule"></div>
  <h3 class="subtitle display" style="top:47px">Bringing Vision to Reality</h3>
  <div class="ring" style="left:83px;top:79px;width:136px;height:136px"></div>
  <div class="hub" style="left:97px;top:93px;width:108px;height:108px;background:linear-gradient(135deg,#7a5a4a 0%,#b59a86 50%,#e2dad2 100%);border:2px solid #fff" role="img" aria-label="Circular photo of a team meeting around a conference table with laptops"></div>
  <div class="pin" style="left:198px;top:97px"></div>
  <div class="pin" style="left:214px;top:124px"></div>
  <div class="pin" style="left:216px;top:152px"></div>
  <div class="pin" style="left:203px;top:182px"></div>
  <div class="node" style="left:207px;top:70px"><svg width="12" height="12" viewBox="0 0 12 12"><rect x="5" y="1" width="6" height="5" fill="none" stroke="#F28444" stroke-width="1.2"/><circle cx="3" cy="4" r="1.5" fill="#F28444"/><rect x="1.5" y="6" width="3" height="5" fill="#F28444"/></svg></div>
  <div class="node" style="left:226px;top:109px"><svg width="12" height="12" viewBox="0 0 12 12"><circle cx="6" cy="3" r="2" fill="#F28444"/><path d="M1 9l3 2h5l2-3" fill="none" stroke="#F28444" stroke-width="1.4"/></svg></div>
  <div class="node" style="left:226px;top:148px"><svg width="12" height="12" viewBox="0 0 12 12"><path d="M6 1a3.5 3.5 0 0 0-2 6.3V9h4V7.3A3.5 3.5 0 0 0 6 1z" fill="#F28444"/><rect x="4.5" y="10" width="3" height="1.2" fill="#F28444"/></svg></div>
  <div class="node" style="left:209px;top:190px"><svg width="12" height="12" viewBox="0 0 12 12"><rect x="4.5" y="1" width="3" height="3" fill="#F28444"/><rect x="1" y="8" width="3" height="3" fill="#F28444"/><rect x="8" y="8" width="3" height="3" fill="#F28444"/><path d="M6 4v2M2.5 8V6h7v2" fill="none" stroke="#F28444" stroke-width="1"/></svg></div>
  <p class="node-label" style="left:244px;top:79px">Final deliverable presentation</p>
  <p class="node-label" style="left:261px;top:117px">Implementation support</p>
  <p class="node-label" style="left:261px;top:156px">Knowledge transfer</p>
  <p class="node-label" style="left:244px;top:198px">Impact measurement framework</p>
  <div class="footer-bar"><span class="mail-dot"></span>support@dralmorrow.com<span class="page-no">06</span></div>
  <div class="brand footer-brand">Dr ALMorrow</div>
</section>

<!-- 07 Evolution & Growth -->
<section class="slide col-r row3">
  <h2 class="slide-title display">Evolution &amp; <span class="hl">Growth</span></h2>
  <div class="title-rule"></div>
  <div class="photo" style="left:25px;top:52px;width:196px;height:156px;background:linear-gradient(180deg,#cfd6df 0%,#9aa3ae 45%,#7a4f33 80%,#5c3a26 100%)" role="img" aria-label="Photo of a group seated at a long conference table with laptops in a bright office"></div>
  <h3 class="abs display" style="left:242px;top:47px;font-size:12px;color:var(--navy)">Sustaining Long-Term Success</h3>
  <ul class="bullet-list small-list" style="top:65px">
    <li style="margin-bottom:1.5px">Project success celebration</li>
    <li style="margin-bottom:1.5px">Future opportunities exploration</li>
    <li style="margin-bottom:1.5px">Partnership evolution planning</li>
    <li>Continuous improvement recommendations</li>
  </ul>
  <h3 class="abs display" style="left:242px;top:113px;font-size:12px;color:var(--navy)">Why Partner With Us?</h3>
  <ul class="bullet-list small-list" style="top:130px;width:185px">
    <li style="margin-bottom:3px"><b>EXPERTISE:</b> Our diverse team of innovative global public health professionals, specialized in epidemiology and health communication</li>
    <li style="margin-bottom:3px"><b>IMPACT:</b> Proven track record of transforming complex health data into accessible information</li>
    <li style="margin-bottom:3px"><b>INNOVATION:</b> Custom solutions tailored to BIPOC community needs</li>
    <li><b>PARTNERSHIP:</b> Collaborative approach ensuring lasting results</li>
  </ul>
  <div class="footer-bar"><span class="mail-dot"></span>support@dralmorrow.com<span class="page-no">07</span></div>
  <div class="brand footer-brand">Dr ALMorrow</div>
</section>

<!-- 08 Closing -->
<section class="slide col-r row4">
  <div class="close-top"></div>
  <div class="abs" style="left:280px;top:16px;width:139px;height:180px;background:linear-gradient(180deg,#3a3a52 0%,#2a2a38 60%,#1e1e2a 100%);border-radius:60px 60px 0 0" role="img" aria-label="Portrait photo of the firm's founder in a dark blazer"></div>
  <h2 class="close-title display">Ready to Transform<br>Your Health Communication?</h2>
  <p class="close-text">Contact us to begin your journey toward more effective, equitable health communication.</p>
  <div class="mail-pill"><svg width="7" height="5" viewBox="0 0 7 5"><rect width="7" height="5" fill="#fff"/><path d="M0 0l3.5 2.6L7 0" fill="none" stroke="#F24C27" stroke-width=".8"/></svg>support@dralmorrow.com</div>
  <div class="brand center-brand" style="top:208px">Dr ALMorrow</div>
</section>

</body>
</html>
```